Awesome Frosted Plastic Business Card Needed

I am looking for a business card for my company: Tarvel Automation.
The business card should be the standard US size 3.5" x 2"

Tarvel Automation is a high tech distributor of products for the Automation industry. We work with customers to find the right products (motors, amplifiers, controls, gear boxes, robotic arms, bearings, encoders, actuators, ball screws, HMI's, etc.) to fit their application. We then work with them to install and support these products.

I would like the design to communicate the following:
-Our Technical (engineering) services
-Our experience in the industry
-Value (our products come with service and support, our competitors just have products)
-Partnership (we want to partner with our customers to help them succeed and grow)
-That we are a modern company - using social media to communicate with clients
-The best products

One design idea I liked is attached. It shows a ring with 6 circles. Each circle has an icon. For the above you could have an icon depicting an engineer/engineering, an icon depicting knowledge or experience, an icon of two hands shaking depicting partnership, an icon of a robotic arm to show we are high tech, etc...

This is just one idea I saw, I am in no way locked into it. Please feel free to be creative.

Also, this business card will be 2-sided and printed on a clear (frosted) plastic card. So, understand that what is printed on one side will show through to the other. If you put text on a solid color background, the text will not show through, but the solid background will.

I will need a white space 360px X 360px left free on one side. I plan to place a QR code in this space. (I have attached a sample QR code if you would like to incorporate it in the design - it needs to be resized to 360 x 360)

My contact information for the business card is as follows:

Name: Dan Keswick
Title: President
email: dkeswick@tarvelautomation.example
website: www.tarvelautomation.example
Office: 555.418.2700
Desk: 555.418.2703
Cell: 555.902.4471
No address information is needed at this time.

As you will see, my website is not yet up and running. However, a very similar company in a different part of the company is Norbex: http://www.norbex-systems.example/

You can take a look at their website to get an idea about what Tarvel Automation does.

Thanks,

-Dan

Industry/Entity Type

Business

```html
<!DOCTYPE html>
<html lang="en">
<head>
<meta charset="utf-8">
<title>Tarvel Automation – Business Card</title>
<link rel="stylesheet" href="https://fonts.googleapis.com/css2?family=Exo+2:wght@600;700&family=Open+Sans:wght@400;600&display=swap">
<style>
  :root {
    --page: #e4e2df;
    --frost-top: #d9d8d6;
    --frost-bottom: #bdbcba;
    --band: #232222;
    --band-edge: #141313;
    --ink: #3a3a3a;
    --accent: #d4232b;
    --white: #ffffff;
    --muted: #c9c9c9;
  }
  * { box-sizing: border-box; margin: 0; padding: 0; }
  html, body {
    width: 1200px; height: 560px; overflow: hidden;
    background: var(--page);
    font-family: "Open Sans", Arial, sans-serif;
  }
  .sheet {
    position: relative; width: 1200px; height: 560px;
    display: flex; justify-content: center; align-items: center; gap: 40px;
  }
  .card {
    position: relative; width: 540px; height: 310px;
    border-radius: 6px; overflow: hidden;
    background: linear-gradient(180deg, var(--frost-top), var(--frost-bottom));
    box-shadow: 0 10px 28px rgba(0,0,0,0.18);
  }
  .card__band {
    position: absolute; left: 0; right: 0; top: 108px; height: 150px;
    background: linear-gradient(180deg, var(--band), var(--band-edge));
  }
  .card__foot {
    position: absolute; left: 0; right: 0; bottom: 0; height: 52px;
    display: flex; align-items: center; padding: 0 28px; gap: 14px;
  }

  /* Brand name */
  .brand {
    position: absolute; left: 28px; top: 30px;
    display: flex; align-items: center; gap: 12px;
  }
  .brand__square { width: 40px; height: 40px; background: var(--accent); }
  .brand__name {
    font-family: "Exo 2", Arial, sans-serif; font-weight: 700;
    font-size: 30px; line-height: 1; color: var(--ink); white-space: nowrap;
  }
  .brand--ghost { left: auto; right: 28px; transform: scaleX(-1); opacity: 0.3; }

  /* Front contact band */
  .contact {
    position: absolute; inset: 0;
    display: grid; grid-template-columns: 1fr 1.3fr 1fr;
    align-items: start; padding-top: 22px; text-align: center;
  }
  .contact__icon { width: 38px; height: 38px; margin: 0 auto 14px; display: block; }
  .contact__name {
    font-family: "Exo 2", Arial, sans-serif; font-weight: 700;
    font-size: 18px; color: var(--white); letter-spacing: 0.5px; white-space: nowrap;
  }
  .contact__title { font-size: 8px; letter-spacing: 1px; color: var(--muted); margin-top: 2px; }
  .contact__line { font-size: 11px; line-height: 16px; color: var(--white); white-space: nowrap; }

  /* Follow strip */
  .follow { line-height: 1; }
  .follow__label { font-size: 11px; font-weight: 600; letter-spacing: 1px; color: #555; }
  .follow__sub { font-size: 6.5px; letter-spacing: 0.5px; color: #666; margin-top: 3px; }
  .follow__dots { display: flex; gap: 10px; }
  .follow__dot { width: 12px; height: 12px; border-radius: 50%; background: #6e6e6e; }
  .card__foot--ghost { justify-content: flex-end; transform: scaleX(-1); opacity: 0.3; }

  /* Back: reserved code space and services */
  .code-space {
    position: absolute; left: 14px; top: 12px;
    width: 126px; height: 126px; background: var(--white);
  }
  .services {
    position: absolute; top: 0; bottom: 0; left: 150px; right: 10px;
    display: flex; flex-direction: column;
    justify-content: center; align-items: center; text-align: center; color: var(--white);
  }
  .services__title {
    font-family: "Exo 2", Arial, sans-serif; font-weight: 600;
    font-size: 18px; margin-bottom: 6px;
  }
  .services__line { font-size: 8.5px; line-height: 14px; white-space: nowrap; }
</style>
</head>
<body>
<main class="sheet">

  <section class="card card--front" aria-label="Card front">
    <div class="brand">
      <span class="brand__square"></span>
      <span class="brand__name">Tarvel Automation</span>
    </div>

    <div class="card__band">
      <div class="contact">
        <div class="contact__col">
          <svg class="contact__icon" viewBox="0 0 38 38" aria-hidden="true">
            <circle cx="19" cy="19" r="18" fill="#fff"/>
            <circle cx="19" cy="15" r="5.5" fill="#232222"/>
            <path d="M9.5 28c1.5-5.5 5-8 9.5-8s8 2.5 9.5 8z" fill="#232222"/>
          </svg>
          <div class="contact__name">DAN KESWICK</div>
          <div class="contact__title">PRESIDENT</div>
        </div>
        <div class="contact__col">
          <svg class="contact__icon" viewBox="0 0 38 38" aria-hidden="true">
            <circle cx="19" cy="19" r="18" fill="#fff"/>
            <g fill="none" stroke="#232222" stroke-width="1.6">
              <circle cx="19" cy="19" r="10"/>
              <ellipse cx="19" cy="19" rx="4.5" ry="10"/>
              <line x1="9" y1="19" x2="29" y2="19"/>
              <path d="M10.5 14h17M10.5 24h17"/>
            </g>
          </svg>
          <div class="contact__line">dkeswick@tarvelautomation.example</div>
          <div class="contact__line">www.tarvelautomation.example</div>
        </div>
        <div class="contact__col">
          <svg class="contact__icon" viewBox="0 0 38 38" aria-hidden="true">
            <circle cx="19" cy="19" r="18" fill="#fff"/>
            <rect x="13" y="8" width="12" height="22" rx="2" fill="#232222"/>
            <rect x="14.5" y="11" width="9" height="14" fill="#fff"/>
            <circle cx="19" cy="27.5" r="1" fill="#fff"/>
          </svg>
          <div class="contact__line">555.418.2700</div>
          <div class="contact__line">555.902.4471</div>
        </div>
      </div>
    </div>

    <div class="card__foot">
      <div class="follow">
        <div class="follow__label">FOLLOW US</div>
        <div class="follow__sub">ON SOCIAL NETWORK</div>
      </div>
      <div class="follow__dots">
        <span class="follow__dot"></span><span class="follow__dot"></span>
        <span class="follow__dot"></span><span class="follow__dot"></span>
      </div>
    </div>
  </section>

  <section class="card card--back" aria-label="Card back">
    <div class="brand brand--ghost">
      <span class="brand__square"></span>
      <span class="brand__name">Tarvel Automation</span>
    </div>

    <div class="card__band">
      <div class="code-space" role="img" aria-label="Blank space reserved for the QR code"></div>
      <div class="services">
        <h2 class="services__title">Areas of Excellence</h2>
        <p class="services__line">Machine Control | Motion Control | Actuators, Stages, XY Tables, Gantries</p>
        <p class="services__line">Mechanical Assemblies &amp; Systems | Pneumatics</p>
        <p class="services__line">Air Compressors &amp; Vacuum Pumps | Intelligent Sensors &amp; Vision Systems</p>
      </div>
    </div>

    <div class="card__foot card__foot--ghost">
      <div class="follow">
        <div class="follow__label">FOLLOW US</div>
        <div class="follow__sub">ON SOCIAL NETWORK</div>
      </div>
      <div class="follow__dots">
        <span class="follow__dot"></span><span class="follow__dot"></span>
        <span class="follow__dot"></span><span class="follow__dot"></span>
      </div>
    </div>
  </section>

</main>
</body>
</html>
```